Modern Verdell Tree Care Website

I need a website for a full service Tree Care company. The company provides tree pruning, tree removal, tree preservation, emergency services, stump grinding, and emergency tree services.

Target Market(s)

Customers that need tree services

Industry/Entity Type

Landscaping, Tree Services

Coding

Coded - Design and coding required

Number of Pages Required

5+ page

Font styles to use
Sans Serif

Requirements
Must have
• Good clean design that showcases the services the company provides.
Nice to have
• Services page; contact form, blog, home page, about page

```html
<!DOCTYPE html>
<html lang="en">
<head>
<meta charset="utf-8">
<title>Verdell Tree Care</title>
<link href="https://fonts.googleapis.com/css2?family=Poppins:wght@400;500;600;700&family=Montserrat:wght@400;500&display=swap" rel="stylesheet">
<style>
:root{
  --green:#8cc63f;
  --green-dark:#6ea52b;
  --orange:#fbb034;
  --tan:#c4956b;
  --slate:#5d6a70;
  --ink:#2b2b2b;
  --muted:#7a7a7a;
  --line:#e3e3e3;
  --white:#ffffff;
}
*{margin:0;padding:0;box-sizing:border-box}
html,body{width:1200px;height:5168px;overflow:hidden}
body{position:relative;background:var(--white);font-family:'Poppins',sans-serif;color:var(--ink)}
a{text-decoration:none}
.abs{position:absolute}
.photo{position:absolute;border-radius:6px}
/* header */
.site-header{position:absolute;left:0;top:0;width:1200px;height:108px;background:#fff;display:flex;align-items:center;justify-content:space-between;padding:0 72px}
.brand{display:flex;align-items:center;gap:14px;font-family:'Poppins',sans-serif;font-weight:700;font-size:26px;color:var(--slate);white-space:nowrap}
.brand-dot{width:36px;height:36px;border-radius:50%;background:var(--green);flex:none}
.main-nav{display:flex;gap:32px;font-size:13px;color:var(--ink)}
.main-nav a{color:inherit;padding-bottom:14px}
.main-nav a.active{color:var(--green);border-bottom:2px solid var(--green)}
/* hero */
.hero{position:absolute;left:0;top:108px;width:1200px;height:740px;background:linear-gradient(180deg,#3f7a2a 0%,#6d9a35 45%,#7fae3c 70%,#8dba48 100%)}
.hero-title{position:absolute;top:262px;width:1200px;text-align:center;color:#fff;font-size:50px;font-weight:600;text-shadow:0 2px 6px rgba(0,0,0,.4)}
.hero-sub{position:absolute;top:326px;width:1200px;text-align:center;color:#fff;font-size:30px;text-shadow:0 2px 6px rgba(0,0,0,.4)}
.btn{display:inline-block;background:var(--green);color:#fff;border-radius:30px;font-weight:500;text-align:center;text-decoration:none}
.hero .btn{position:absolute;left:502px;top:390px;width:196px;height:52px;line-height:48px;font-size:14px;border:2px solid #fff}
/* features */
.features{position:absolute;left:108px;top:752px;width:982px;height:218px;display:flex}
.feature{flex:1;text-align:center;color:#fff;padding:26px 16px 0}
.feature .ring{width:60px;height:60px;border:3px solid #fff;border-radius:50%;margin:0 auto 16px;display:flex;align-items:center;justify-content:center}
.feature .ring span{width:30px;height:30px;border:2px solid #fff;border-radius:50%}
.feature h3{font-size:12px;font-weight:500;margin-bottom:6px;line-height:14px}
.feature p{font-size:12px;line-height:17px}
/* section headings */
.heading h2{font-size:46px;font-weight:600;color:var(--slate);line-height:50px}
.heading .sub{font-family:'Montserrat',sans-serif;font-size:18px;letter-spacing:2px;color:var(--green);display:flex;align-items:center;gap:12px}
.heading .sub i{display:block;height:3px;width:72px;background:var(--green)}
.heading.center{text-align:center}
.heading.center .sub{justify-content:center}
/* about */
.about-text{position:absolute;left:124px;top:1170px;width:556px;font-family:'Montserrat',sans-serif;font-size:13px;line-height:27px;color:#333}
.about-text p+p{margin-top:27px}
/* services */
.service-card{position:absolute;width:300px;height:420px;background:#fff;border-radius:14px;box-shadow:0 2px 10px rgba(0,0,0,.15)}
.service-card .icon{position:absolute;left:24px;top:16px;width:84px;height:84px;border-radius:50%;border:3px solid var(--green);display:flex;align-items:center;justify-content:center}
.service-card .icon span{width:60px;height:60px;border-radius:50%;background:var(--green)}
.service-card h3{position:absolute;left:24px;top:114px;font-size:21px;font-weight:500;white-space:nowrap}
.service-card .photo{left:8px;top:166px;width:284px;height:244px;border-radius:8px}
.plus{position:absolute;right:28px;top:144px;width:44px;height:44px;border-radius:50%;background:var(--green);border:3px solid #fff;color:#fff;font-size:28px;line-height:36px;text-align:center;z-index:2}
/* cta */
.cta{position:absolute;left:0;top:2720px;width:1200px;height:472px;background:linear-gradient(90deg,#86c03c 0%,#8cc63f 35%,#6f8f45 60%,#5a6a3a 100%)}
.cta h2{position:absolute;left:72px;top:100px;color:#fff;font-size:44px;font-weight:600;line-height:56px;text-shadow:0 2px 5px rgba(0,0,0,.35)}
.cta .btn{position:absolute;left:78px;top:296px;width:246px;height:74px;line-height:74px;background:#fff;color:var(--ink);border-radius:40px;font-size:22px}
/* blog */
.blog-card{position:absolute;width:280px;height:420px;background:#fff;border-radius:14px;box-shadow:0 2px 10px rgba(0,0,0,.15);text-align:center}
.blog-card .photo{left:8px;top:8px;width:264px;height:204px;border-radius:12px}
.blog-card h3{position:absolute;top:236px;width:100%;font-size:16px;font-weight:500;line-height:22px;padding:0 22px}
.blog-card p{position:absolute;top:290px;width:100%;font-family:'Montserrat',sans-serif;font-size:12px;line-height:20px;color:var(--muted);padding:0 22px}
.blog-card .btn{position:absolute;left:88px;top:356px;width:104px;height:26px;line-height:26px;font-size:11px}
.dots{position:absolute;left:548px;top:3924px;display:flex;gap:10px;align-items:center}
.dots i{display:block;width:10px;height:10px;border-radius:50%;background:#ccc}
.dots i.on{width:28px;height:5px;border-radius:3px;background:var(--orange)}
/* contact */
.field{position:absolute;border:1px solid var(--line);box-shadow:0 1px 6px rgba(0,0,0,.1);background:#fff;font-family:'Montserrat',sans-serif;font-size:13px;color:#888;padding:14px 20px}
.submit{position:absolute;left:632px;top:4534px;width:168px;height:54px;line-height:54px;font-size:17px}
/* footer */
.footer{position:absolute;left:0;top:4690px;width:1200px;height:478px;background:var(--green)}
.newsletter{position:absolute;left:204px;top:56px;width:792px;height:110px;background:var(--orange);border-radius:56px}
.newsletter h3{position:absolute;left:36px;top:33px;font-size:31px;font-weight:500;color:#fff;white-space:nowrap}
.newsletter .input{position:absolute;left:412px;top:36px;width:350px;height:38px;background:#fff;border-radius:20px;font-size:10px;color:#555;padding:12px 22px}
.newsletter .btn{position:absolute;left:654px;top:36px;width:108px;height:38px;line-height:38px;font-size:12px}
.footer h4{position:absolute;font-size:17px;font-weight:500;color:#fff}
.quick{position:absolute;left:206px;top:256px;list-style:none;font-size:13px;color:#fff;line-height:26px}
.quick li::before{content:"";display:inline-block;width:8px;height:8px;border-radius:50%;background:var(--orange);margin-right:12px}
.footer-brand{position:absolute;left:396px;top:244px;display:flex;align-items:center;gap:12px;font-size:28px;font-weight:700;color:var(--slate);white-space:nowrap}
.footer-brand .brand-dot{width:44px;height:44px;background:#fff}
.contact-item{position:absolute;left:780px;display:flex;gap:14px;font-size:13px;color:#fff;line-height:16px}
.contact-item .ic{width:26px;height:26px;border-radius:50%;background:var(--orange);flex:none;display:flex;align-items:center;justify-content:center}
.footer-bottom{position:absolute;left:0;top:440px;width:1200px;height:38px;background:var(--green-dark);font-size:12px;color:#fff;padding:10px 76px}
.socials{position:absolute;right:72px;top:7px;display:flex;gap:8px}
.socials i{display:block;width:24px;height:24px;border-radius:50%;border:1.5px solid #fff}
</style>
</head>
<body>

<header class="site-header">
  <div class="brand"><span class="brand-dot"></span>Verdell Tree Care</div>
  <nav class="main-nav">
    <a class="active" href="#">HOME</a><a href="#">ABOUT US</a><a href="#">SERVICES ▾</a><a href="#">BLOG</a><a href="#">CONTACT US</a>
  </nav>
</header>

<section class="hero" role="img" aria-label="Wide spreading tree on a green lawn in a park">
  <h1 class="hero-title">Call Verdell for All Your Tree Care Needs</h1>
  <p class="hero-sub">Serving Lafayette and surrounding areas</p>
  <a class="btn" href="#">LEARN MORE</a>
</section>

<div class="features">
  <div class="feature" style="background:var(--tan)"><div class="ring"><span></span></div><h3>LICENSED AND INSURED</h3><p>Lorem ipsum dolor sit amet, consectetur adip iscing elit.</p></div>
  <div class="feature" style="background:var(--green)"><div class="ring"><span></span></div><h3>24-HOURS EMERGENCY SERVICES</h3><p>Lorem ipsum dolor sit amet, consectetur adip</p></div>
  <div class="feature" style="background:var(--orange)"><div class="ring"><span></span></div><h3>LOCALLY OWNED &amp; OPERATED</h3><p>Lorem ipsum dolor sit amet, consectetur adip</p></div>
  <div class="feature" style="background:var(--slate)"><div class="ring"><span></span></div><h3>PROFESSIONAL WORK</h3><p>Lorem ipsum dolor sit amet, consectetur adip iscing elit.</p></div>
  <div class="feature" style="background:var(--green)"><div class="ring"><span></span></div><h3>FREE ESTIMATES</h3><p>Lorem ipsum dolor sit amet, consectetur adip iscing elit.</p></div>
</div>

<section class="about">
  <div class="heading abs" style="left:124px;top:1068px"><h2>ABOUT US</h2><div class="sub">WHO WE ARE <i></i></div></div>
  <div class="about-text">
    <p>At Verdell Tree Care, we are more than just a tree service company, we are stewards of our beautiful trees. With a passion deeply rooted in arboriculture, we embark on a mission to promote the health, beauty, and safety of your trees and landscapes.</p>
    <p>Whether it's expert tree trimming to enhance aesthetics, meticulous tree removal to mitigate hazards, or comprehensive tree health assessments to ensure safety, we approach each task with unwavering dedication and attention to detail.</p>
  </div>
  <a class="btn abs" href="#" style="left:124px;top:1402px;width:156px;height:48px;line-height:48px;font-size:12px">READ MORE</a>
  <div class="photo" role="img" aria-label="Large tree canopy photo" style="left:726px;top:1102px;width:350px;height:348px;border-radius:0;background:linear-gradient(160deg,#5f8d3a,#2f4a22)"></div>
</section>

<section class="services">
  <div class="heading center abs" style="left:0;top:1594px;width:1200px"><h2>OUR SERVICES</h2><div class="sub"><i></i> WHO WE PROVIDE <i></i></div></div>

  <article class="service-card" style="left:124px;top:1730px"><div class="icon"><span></span></div><h3>Tree Pruning</h3><div class="plus">+</div><div class="photo" role="img" aria-label="Gloved hands pruning branches against the sky" style="background:linear-gradient(180deg,#b8cde6,#6e7f8f)"></div></article>
  <article class="service-card" style="left:448px;top:1730px"><div class="icon"><span></span></div><h3>Tree Removal</h3><div class="plus">+</div><div class="photo" role="img" aria-label="Chainsaw cutting a tree trunk in a forest" style="background:linear-gradient(180deg,#6d5a42,#3e3429)"></div></article>
  <article class="service-card" style="left:772px;top:1730px"><div class="icon"><span></span></div><h3>Tree Preservation</h3><div class="plus">+</div><div class="photo" role="img" aria-label="Arborists inspecting trees in a forest" style="background:linear-gradient(180deg,#7a8a5a,#4b4a35)"></div></article>

  <article class="service-card" style="left:124px;top:2172px"><div class="icon"><span></span></div><h3>Emergency Services</h3><div class="plus">+</div><div class="photo" role="img" aria-label="Fallen trees after a storm" style="background:linear-gradient(180deg,#8fa07a,#4f5d3a)"></div></article>
  <article class="service-card" style="left:448px;top:2172px"><div class="icon"><span></span></div><h3>Stump Grinding</h3><div class="plus">+</div><div class="photo" role="img" aria-label="Workers operating an orange log processing machine" style="background:linear-gradient(180deg,#5a5a4c,#b5582a)"></div></article>
  <article class="service-card" style="left:772px;top:2172px"><div class="icon"><span></span></div><h3>Emergency Tree Services</h3><div class="plus">+</div><div class="photo" role="img" aria-label="Broken tree trunk lying in a forest" style="background:linear-gradient(180deg,#aab39a,#5e6a4a)"></div></article>
</section>

<section class="cta" role="img" aria-label="Worker cutting a log with a chainsaw">
  <h2>CALL US TODAY TO SEE HOW<br>WE CAN HELP YOU WITH ALL<br>OF YOUR TREE NEEDS:</h2>
  <a class="btn" href="#">CONTACT US</a>
</section>

<section class="blog">
  <div class="heading center abs" style="left:0;top:3306px;width:1200px"><h2>OUR BLOG</h2><div class="sub"><i style="width:54px"></i> LATEST NEWS <i style="width:54px"></i></div></div>

  <article class="blog-card" style="left:148px;top:3436px"><div class="photo" role="img" aria-label="Forestry workers in safety vests among trees" style="background:linear-gradient(180deg,#8c8f78,#4e4a3a)"></div><h3>Lorem ipsum dolor sit amet, consectetur elit dol</h3><p>Lorem ipsum dolor sit amet, con sectetur adipiscing elit, sed do ei</p><a class="btn" href="#">Read More</a></article>
  <article class="blog-card" style="left:460px;top:3436px"><div class="photo" role="img" aria-label="Crew clearing a fallen birch tree" style="background:linear-gradient(180deg,#7d7a66,#4a4538)"></div><h3>Lorem ipsum dolor sit amet, consectetur elit dol</h3><p>Lorem ipsum dolor sit amet, con sectetur adipiscing elit, sed do ei</p><a class="btn" href="#">Read More</a></article>
  <article class="blog-card" style="left:772px;top:3436px"><div class="photo" role="img" aria-label="Chainsaw cutting into a stump" style="background:linear-gradient(180deg,#a07a5a,#5a4330)"></div><h3>Lorem ipsum dolor sit amet, consectetur elit dol</h3><p>Lorem ipsum dolor sit amet, con sectetur adipiscing elit, sed do ei</p><a class="btn" href="#">Read More</a></article>

  <div class="dots"><i class="on"></i><i></i><i></i><i></i></div>
</section>

<section class="contact">
  <div class="photo" role="img" aria-label="Misty forest of tall trees" style="left:102px;top:4128px;width:426px;height:444px;border-radius:14px;background:linear-gradient(180deg,#9fb0a0,#3f5a3e)"></div>
  <div class="heading abs" style="left:628px;top:4082px"><h2>CONTACT US</h2><div class="sub">GET IN TOUCH <i style="width:144px"></i></div></div>
  <div class="field" style="left:632px;top:4208px;width:224px;height:44px">First Name:</div>
  <div class="field" style="left:874px;top:4208px;width:224px;height:44px">Last Name:</div>
  <div class="field" style="left:632px;top:4274px;width:224px;height:44px">Phone:</div>
  <div class="field" style="left:874px;top:4274px;width:224px;height:44px">Email:</div>
  <div class="field" style="left:632px;top:4342px;width:466px;height:142px">Mesage:</div>
  <a class="btn submit" href="#">SUBMIT</a>
</section>

<footer class="footer">
  <div class="newsletter"><h3>Our Newsletter Sign Up</h3><div class="input">Enter Email Address</div><a class="btn" href="#">SIGNUP</a></div>

  <h4 style="left:204px;top:216px">QUICK LINKS</h4>
  <ul class="quick"><li>Home</li><li>About Us</li><li>Services</li><li>Blog</li><li>Contact Us</li></ul>

  <div class="footer-brand"><span class="brand-dot"></span>Verdell Tree Care</div>

  <h4 style="left:778px;top:216px">CONTACT US</h4>
  <div class="contact-item" style="top:258px"><span class="ic"><svg width="12" height="12" viewBox="0 0 24 24"><path fill="#fff" d="M6.6 10.8a15 15 0 0 0 6.6 6.6l2.2-2.2c.3-.3.7-.4 1-.2 1.1.4 2.3.6 3.6.6.6 0 1 .4 1 1V20c0 .6-.4 1-1 1A17 17 0 0 1 3 4c0-.6.4-1 1-1h3.5c.6 0 1 .4 1 1 0 1.3.2 2.5.6 3.6.1.3 0 .7-.2 1z"/></svg></span><div>CALL US<br>(555) 014-2739</div></div>
  <div class="contact-item" style="top:310px"><span class="ic"><svg width="12" height="12" viewBox="0 0 24 24"><path fill="#fff" d="M3 5h18v14H3zm2 2v.5l7 4.5 7-4.5V7l-7 4.5z"/></svg></span><div>EMAIL US<br>info@verdelltreecare.com</div></div>
  <div class="contact-item" style="top:358px"><span class="ic"><svg width="12" height="12" viewBox="0 0 24 24"><path fill="#fff" d="M12 2a7 7 0 0 0-7 7c0 5 7 13 7 13s7-8 7-13a7 7 0 0 0-7-7zm0 9.5A2.5 2.5 0 1 1 12 6.5a2.5 2.5 0 0 1 0 5z"/></svg></span><div>Address line here dummy<br>Address line here</div></div>

  <div class="footer-bottom">Copyright ©2024- All Rights Reserved by Company name
    <div class="socials"><i></i><i></i><i></i><i></i></div>
  </div>
</footer>

</body>
</html>
```